Shipping and Logistics, Project

Project description : Company Profile

A total logistics company covering domestic / international freight forwarding, warehouse management services, haulage, supply chain management, transport management & distribution, procurement & assembly services, shipping, chartering & bunker services, project logistics & tax exemption consultancy, oil & gas logistics, halal logistics services & integrated logistics management. We’re a well-established and experienced freight forwarder in Kuala Lumpur, Malaysia. We specialize in customized value-added solution that optimizes your supply chain by trimming inventory, reducing logistics cost and enhancing your customer service levels.

As a member of the Worldwide Parcel and Carriage Alliance which comprise of 170 global freight agents in 80 countries that promotes great handling in cross-trade logistics and freighting. You could rely on our efficiency in handlings of export cargo (FCL, LCL, Bulk and Conventional) between our global network offices worldwide with a total scale of 10,000 groomed specialists in various logistics division working together to ensure delivery task meets with your expectation. With our dedicated qualified and experienced professionals, we are fully committed to serving our clients.

Our generic services are listed below for your reference:

• Air Freight
• Ocean Freight FCL & LCL
• Container Haulage
• Warehousing
• Transportation and Distribution within Malaysia and Thailand
• Cross-Border Road Line-hauls between Thailand, Malaysia, Singapore and Laos
• Customs Brokerage and Forwarding
• Project Cargo Freight Forwarding for setting up of new plants / factories and ad hoc heavy-lift
• Air-Sea-Road-Rail multi-modal options
• Import / Export / Storage / Documentation / Handling of DG / Hazmat
• Vessel and Aircraft Charters

Our Mission
Based on the motto “Quick, Reliable and Polite”, we are dedicated to upholding the following three points corporate philosophy:
1. Adhering to the principle that “the customer always comes first”.
2. Contributing to the development of the local community.
3. Making it our duty to be responsible and sincere.

Our Edge
• One-Stop Logistics Solutions
• Extensive Network Throughout Malaysia
• Highly Qualified and Experienced Pool of Professionals
• Comprehensive IT Solutions
• Innovative and Customer-focused Solutions
• Flexible and Consistent in Managing Exceptions
• Total Supply Chain Visibility

Target Market
1. We sell the logistics services to all the industry in Malaysia and Worldwide. (ONE Stop Logistics Solutions)

Competitor
1. TR Valmont
2. Corvessa Transport
3. Brandt + Loewe
4. FELRO
5. QTV
6. Routemarks
7. Ilto Logistics

Rules for Picking a Company Name
1. Unique and unforgettable
2. Avoid unusual spellings
3. Easy to pronounce and remember
4. Keep it simple
5. Make some sense
6. Give a clue

Rules for Picking a Company Logo
4. Keep it simple
5. Make some sense
6. Give a clue

1. Simplicity
2. Memorability
3. Originality
4. Modern Yet Timeless
5. Balance
6. Complementary
7. Versatility

Stationery Information
1. Company Name : ZENFreight Solutions Sdn Bhd
2. Company Registration : 2837165-W
3. Address : 42-08, Jalan Cempaka Indah 5, Taman Seri Bayu, 81300 Johor Bahru, Johor, Malaysia.
4. Name : Derek Tan
5. Position : Manager
6. Mobile No : (+6019) 4381907
7. Office No : (+607) 5218764
8. Fax No : Not Available
9. Email Address : derek.tan@zenfreight-solutions.example
10. Web Domain : www.zenfreight-solutions.example
11. Company Slogan : Be Globally Connected

Target Market(s)

Corporate Company

Industry/Entity Type

Shipping and Logistics Industry

Requirements
Must have
• Company Full Name : ZENFREIGHT SOLUTIONS SDN. BHD.
Nice to have
• Keep it simple and unforgettable ...

```html
<!DOCTYPE html>
<html lang="en">
<head>
<meta charset="utf-8">
<title>ZENFreight Solutions – Business Card</title>
<link rel="stylesheet" href="https://fonts.googleapis.com/css2?family=Poppins:wght@400;500;600;700&display=swap">
<style>
  :root {
    --brand-blue: #2e8ad9;
    --ink-dark: #272727;
    --paper: #ffffff;
    --backdrop: #b8b8b8;
    --rule-grey: #6a6a6a;
  }
  * { box-sizing: border-box; margin: 0; padding: 0; }
  html, body {
    width: 1200px; height: 1200px; overflow: hidden;
    background: var(--backdrop);
    font-family: "Poppins", sans-serif;
  }
  .canvas { position: relative; width: 1200px; height: 1200px; }

  .card {
    position: absolute; top: 303px;
    width: 368px; height: 594px; overflow: hidden;
  }

  /* Front side */
  .card-front { left: 200px; background: var(--brand-blue); }
  .front-dark {
    position: absolute; inset: 0;
    background: var(--ink-dark);
    clip-path: polygon(0 86px, 100% 196px, 100% 100%, 0 100%);
  }
  .registration {
    position: absolute; top: 33px; left: 0; right: 0;
    text-align: center; color: var(--paper);
    font-size: 17px; font-weight: 400; letter-spacing: 0.2px;
  }
  .front-name {
    position: absolute; top: 300px; left: 0; right: 0;
    display: flex; align-items: center; justify-content: center; gap: 10px;
    color: var(--paper); font-size: 22px; font-weight: 600; letter-spacing: 0.5px;
  }
  .front-name .mark-square {
    width: 18px; height: 18px; background: var(--brand-blue);
  }
  .tagline {
    position: absolute; top: 532px; left: 0; right: 0;
    text-align: center; color: var(--brand-blue);
    font-size: 17px; font-weight: 500;
  }

  /* Back side */
  .card-back { left: 599px; background: var(--ink-dark); }
  .back-header {
    position: absolute; top: 0; left: 0; right: 0; height: 239px;
    background: var(--paper);
    display: flex; align-items: center; justify-content: center; gap: 12px;
  }
  .back-header .mark-square {
    width: 34px; height: 34px; background: var(--brand-blue); flex: none;
  }
  .company-name {
    color: var(--ink-dark); font-weight: 600; font-size: 17px;
    line-height: 1.25; letter-spacing: 0.6px;
  }
  .header-rule {
    position: absolute; top: 239px; left: 0; right: 0; height: 6px;
    background: var(--brand-blue);
  }
  .header-pointer {
    position: absolute; top: 244px; left: 50%; margin-left: -14px;
    width: 0; height: 0;
    border-left: 14px solid transparent; border-right: 14px solid transparent;
    border-top: 12px solid var(--brand-blue);
  }
  .person-name {
    position: absolute; top: 270px; left: 0; right: 0; text-align: center;
    color: var(--brand-blue); font-size: 25px; font-weight: 600; line-height: 1.2;
  }
  .person-role {
    position: absolute; top: 301px; left: 0; right: 0; text-align: center;
    color: var(--paper); font-size: 16px; font-weight: 400;
  }
  .contact-icons {
    position: absolute; top: 337px; left: 0; right: 0;
    display: flex; align-items: center; justify-content: center; gap: 4px;
  }
  .contact-icons .line { width: 31px; height: 1px; background: var(--paper); opacity: .7; margin: 0 6px; }
  .icon-box {
    width: 25px; height: 25px; background: var(--brand-blue); border-radius: 2px;
    display: flex; align-items: center; justify-content: center;
  }
  .icon-box svg { width: 16px; height: 16px; }
  .contact-list {
    position: absolute; top: 374px; left: 0; right: 0; text-align: center;
    color: var(--paper); font-size: 17px; line-height: 21.7px; font-weight: 400;
  }
  .contact-list .small { font-size: 14.5px; }
  .contact-list .accent { color: var(--brand-blue); }
  .divider {
    position: absolute; top: 477px; left: 89px; width: 195px; height: 1px;
    background: var(--rule-grey);
  }
  .address {
    position: absolute; top: 490px; left: 0; right: 0; text-align: center;
    color: var(--paper); font-size: 16.5px; line-height: 21.7px;
  }
</style>
</head>
<body>
<div class="canvas">

  <section class="card card-front">
    <div class="front-dark"></div>
    <p class="registration">Registration : 2837165-W</p>
    <div class="front-name"><span class="mark-square"></span>ZENFREIGHT</div>
    <p class="tagline">BE GLOBALLY CONNECTED</p>
  </section>

  <section class="card card-back">
    <header class="back-header">
      <span class="mark-square"></span>
      <p class="company-name">ZENFREIGHT<br>SOLUTIONS SDN. BHD.</p>
    </header>
    <div class="header-rule"></div>
    <div class="header-pointer"></div>

    <h1 class="person-name">DEREK TAN</h1>
    <p class="person-role">MANAGER</p>

    <div class="contact-icons">
      <span class="line"></span>
      <span class="icon-box" aria-label="Mobile">
        <svg viewBox="0 0 16 16"><rect x="4.5" y="1.5" width="7" height="13" rx="1" fill="none" stroke="#fff" stroke-width="1.4"/><circle cx="8" cy="12.3" r=".8" fill="#fff"/></svg>
      </span>
      <span class="icon-box" aria-label="Office phone">
        <svg viewBox="0 0 16 16"><path d="M2 6c0-2 3-3 6-3s6 1 6 3v1h-3V5.5H5V7H2z" fill="#fff"/><rect x="3.5" y="8" width="9" height="5" rx="1" fill="#fff"/></svg>
      </span>
      <span class="icon-box" aria-label="Email">
        <svg viewBox="0 0 16 16"><rect x="2" y="4" width="12" height="8.5" fill="none" stroke="#fff" stroke-width="1.3"/><path d="M2 4l6 5 6-5" fill="none" stroke="#fff" stroke-width="1.3"/></svg>
      </span>
      <span class="icon-box" aria-label="Website">
        <svg viewBox="0 0 16 16"><circle cx="8" cy="8" r="6" fill="none" stroke="#fff" stroke-width="1.3"/><path d="M2 8h12M8 2c-3 3.5-3 8.5 0 12M8 2c3 3.5 3 8.5 0 12" fill="none" stroke="#fff" stroke-width="1"/></svg>
      </span>
      <span class="line"></span>
    </div>

    <div class="contact-list">
      <p>(+6019) 4381907</p>
      <p>(+607) 5218764</p>
      <p class="small">derek.tan@zenfreight-solutions.example</p>
      <p class="small">www.<span class="accent">zenfreight-solutions</span>.example</p>
    </div>

    <div class="divider"></div>

    <address class="address" style="font-style:normal">
      42-08, Jalan Cempaka Indah 5<br>
      Taman Seri Bayu, 81300 Johor<br>
      Bahru, Johor, Malaysia
    </address>
  </section>

</div>
</body>
</html>
```